Letterhead Design for Law Firm

**Edit: I have added the photo of a bottom that I like.

------
We are looking for a re-design of our new letterhead. The letterhead is for a law firm and will be used for digital and traditionally printed correspondence.

Here are some suggestions:

- Please use colours are #8ec900 and simple black.
- Please do not use any type of "waves" at the bottom of the page. This is not in style at all.
- Please stay modern yet conservative.
- Please use font Segoe UI Light or similar if you can
- Avoid clipart or illustrations.
- Utilize ample white space in the layout so the design looks clean and information is easy to read at a glance. Don't overcrowd the letterhead.
- Make sure the letterhead design is consistent with our brand identity (see corvelith.ca)
-Please, no black headers or footers.

I am attaching my current letterhead and signature for your convenience.

Remember, the letterhead is an extension of our professional identity. We are a successful firm and trial lawyers who correspond with insurers, judges, lawyers, courts, clients, etc. Make it new, modern, attractive, yet powerful and conservative.

It needs to be easily printable. I would like the bleed removed in print so the black bar the bottom crosses the page (but the text is not near the edges)
Updates

Low design quality

Target Market(s)

Clients, Government Offices, Judiciary, Lawyers, Insurance Companies, Colleagues.

Industry/Entity Type

Law

Other font styles liked:
• Segoe UI LIght, Calibri Light,

Colors
00AB8E
00BBA5
67D7C9
C6EFE9
E9F9F6

Requirements
Must have
• Everything that is on the letterhead now.
Nice to have
• Cutting Edge design, yet conservative.
Should not have
• law firm cliche design, images,

```html
<!DOCTYPE html>
<html lang="en">
<head>
<meta charset="utf-8">
<title>Varenne Personal Injury Lawyers – Letterhead</title>
<link rel="stylesheet" href="https://fonts.googleapis.com/css2?family=Noto+Sans:wght@400;600;700&display=swap">
<style>
  :root {
    --brand-green: #8ec21f;
    --ink: #111111;
    --text: #2a2a2a;
    --paper: #faf8f9;
    --backdrop: #e9e7e4;
  }
  * { margin: 0; padding: 0; box-sizing: border-box; }
  html, body {
    width: 1200px; height: 1111px; overflow: hidden;
    background: var(--backdrop);
    font-family: "Noto Sans", "Segoe UI", sans-serif;
    color: var(--text);
  }
  .letterhead {
    position: absolute; left: 185px; top: 20px;
    width: 830px; height: 1071px;
    background: var(--paper);
    box-shadow: 0 2px 10px rgba(0,0,0,0.12);
    overflow: hidden;
  }
  .firm-name {
    position: absolute; left: 44px; top: 40px;
    color: var(--ink); font-weight: 400; line-height: 1;
  }
  .firm-name .name { display: block; font-size: 58px; letter-spacing: 1px; }
  .firm-name .practice { display: block; font-size: 16.5px; letter-spacing: 2.4px; margin-top: 12px; }

  .contact {
    position: absolute; left: 614px; top: 47px;
    border-left: 3px solid var(--brand-green);
    padding-left: 9px; height: 210px;
    font-size: 11.3px; line-height: 15.6px; color: var(--text);
  }
  .contact b { font-weight: 700; color: var(--ink); }
  .contact .site-word { color: var(--brand-green); font-weight: 600; }
  .contact .practice-list { margin-top: 15.6px; }

  .letter-body { position: absolute; left: 58px; top: 152px; font-size: 14px; line-height: 18.6px; }
  .letter-body p { position: absolute; left: 0; white-space: nowrap; }
  .strong { font-weight: 600; color: var(--ink); }

  .regarding {
    position: absolute; left: 56px; top: 450px; width: 657px; height: 62px;
    border-bottom: 1px solid var(--ink);
    font-size: 14px; line-height: 18.6px; font-weight: 600; color: var(--ink);
  }
  .regarding .label { position: absolute; left: 2px; top: 0; }
  .regarding .subject { position: absolute; left: 203px; top: 0; white-space: nowrap; }
  .regarding sup { font-size: 9px; line-height: 0; vertical-align: super; }

  .closing { position: absolute; left: 58px; top: 731px; font-size: 14px; line-height: 18.6px; }
  .closing .firm { font-weight: 600; color: var(--ink); }
  .signature-area {
    width: 190px; height: 40px; margin: 16px 0 6px;
    background: linear-gradient(90deg, rgba(17,17,17,0.18), rgba(17,17,17,0.05));
    border-radius: 3px;
  }
  .closing .small { font-size: 12px; line-height: 15.6px; }
  .closing .corp { font-weight: 600; color: var(--ink); }

  .footer-accent {
    position: absolute; left: 0; bottom: 0; width: 830px; height: 240px;
    background: linear-gradient(165deg, rgba(142,194,31,0) 45%, rgba(142,194,31,0.55) 80%, var(--brand-green) 100%);
  }
</style>
</head>
<body>
<main class="letterhead">
  <div class="firm-name">
    <span class="name">VARENNE</span>
    <span class="practice">PERSONAL INJURY LAWYERS</span>
  </div>

  <aside class="contact">
    www.<span class="site-word">CORVELITH</span>.ca<br>
    48 Harbour Lane, Suite 900<br>
    Kingsford, ON&nbsp; K7P 2B6<br>
    <b>T:</b> 613-555-0142<br>
    <b>F:</b> 613-555-0178<br>
    <b>File Clerk:</b> Carla Moretti<br>
    <b>Email:</b> carla@corvelith.ca
    <div class="practice-list">
      <b>Practice Restricted</b><br>
      Serious Personal Injury<br>
      Wrongful Death Litigation<br>
      Long-Term Disability Litigation<br>
      Wrongful Dismissal Litigation<br>
      Employee Terminations
    </div>
  </aside>

  <section class="letter-body">
    <p class="strong" style="top:0">Without Prejudice</p>
    <p style="top:37px">March 13, 2024</p>
    <p class="strong" style="top:74px">By Email</p>
    <p style="top:112px">Northgate Assurance Company<br>Claims Litigation Department<br>250 Ridgeview Road North<br>P.O. Box 4100<br>Elmford, ON&nbsp;&nbsp; N3K 5T2</p>
    <p style="top:223px">Attention:&nbsp; Mr. Dorian Pike</p>
    <p style="top:261px">Mr. Pike:</p>
  </section>

  <div class="regarding">
    <span class="label">Re:</span>
    <span class="subject">Halvorsen v. Marchetti et al.<br>DOL:&nbsp; September 12, 2019<br>Pre-Mediation Settlement Proposal – March 13<sup>th</sup>, 2024</span>
  </div>

  <section class="closing">
    Yours very truly,<br>
    <span class="firm">VARENNE PERSONAL INJURY LAWYERS</span>
    <div class="signature-area" role="img" aria-label="Handwritten signature of Simon J. Varenne"></div>
    Simon J. Varenne<br>
    <span class="small corp">Varenne Law Professional Corporation</span><br>
    <span class="small">/cm</span><br>
    <span class="small">Encl.</span>
  </section>

  <div class="footer-accent" role="img" aria-label="Green decorative footer accent"></div>
</main>
</body>
</html>
```